Creative, fresh business card design for Ripplecraft Facades

We need a fresh, creative business card design for Ripplecraft Facades. We are the manufacturer of Ripplecraft Facades in Australia. Wall panels are 2400 x 1200mm panels made from MDF and feature 3D patterns on the face of the panel. The colours to be used are green, silver/grey and white RGB
Red 187
Green 207
Blue 65.

An idea is to possibly use a watermark of one of our designs as a background (like on the "Grids" design on the left hand side of page 2 of our brochure).

Target Market(s)

Interior designers, architects, builders and home renovators

Industry/Entity Type

Business

Contact Information for Business Card

Details to go on the card are:
Our logo (attached),
Slogan: "Decorative panels for interiors and exteriors",
Contact name,
Position,
Mobile phone number,
Business address,
Business phone,
Business fax,
Website and
Email address.

I have attached a few images of our panels and our brochure for reference.

The colours of the business card should feature our logo colours which are: RGB
Red 187
Green 207
Blue 65

Requirements
Must have
• Very modern fonts and design. Some of the designs shown especially the "Prisms" design which is a popular design.
Nice to have
• Creative but simple design. Very contemporary.
Should not have
• Anything ornate or old fashioned.

```html
<!DOCTYPE html>
<html lang="en">
<head>
<meta charset="utf-8">
<title>Ripplecraft Facades – Business Card</title>
<link href="https://fonts.googleapis.com/css2?family=Open+Sans:wght@400;600;700&display=swap" rel="stylesheet">
<style>
  :root {
    --stage: #000000;
    --card: #f3f3f3;
    --card-back: #efefef;
    --green: #bbcf41;
    --ink: #1f1f1f;
    --ink-soft: #2c2c2c;
    --silver: #8f8f93;
    --relief-light: #fafafa;
    --relief-mid: #e4e4e4;
  }
  * { box-sizing: border-box; margin: 0; padding: 0; }
  html, body {
    width: 1200px; height: 900px; overflow: hidden;
    background: var(--stage);
    font-family: "Open Sans", Arial, sans-serif;
  }
  .stage { position: relative; width: 1200px; height: 900px; }

  .card {
    position: absolute; top: 200px; width: 310px; height: 502px; overflow: hidden;
  }
  .card--front {
    left: 265px; background: var(--card);
    border-radius: 62px 0 62px 0;
  }
  .card--back {
    left: 641px; background: var(--card-back);
    border-radius: 0 62px 0 62px;
  }

  .relief-strip {
    position: absolute; top: 0; bottom: 0;
    background: linear-gradient(160deg, var(--relief-light) 0%, var(--relief-mid) 35%, var(--relief-light) 60%, var(--relief-mid) 100%);
  }
  .card--front .relief-strip { left: 218px; width: 92px; }
  .card--back .relief-strip { left: 0; width: 71px; }

  .brand {
    position: absolute; left: 43px; top: 52px;
    display: flex; align-items: center; gap: 12px;
  }
  .brand__mark { width: 44px; height: 44px; background: var(--green); }
  .brand__name {
    font-weight: 700; font-size: 22px; line-height: 1.1; color: var(--green);
  }

  .person { position: absolute; left: 23px; top: 231px; }
  .person__name { font-weight: 600; font-size: 17px; color: var(--ink); }
  .person__role { font-size: 13px; color: var(--ink-soft); margin-top: 1px; }

  .address {
    position: absolute; left: 23px; top: 297px;
    font-size: 13px; line-height: 16px; color: var(--ink-soft);
  }

  .contacts {
    position: absolute; left: 23px; top: 353px; list-style: none;
    font-size: 13px; color: var(--ink-soft);
  }
  .contacts li { display: flex; align-items: center; height: 20.8px; }
  .contacts svg { width: 11px; height: 11px; margin-right: 8px; fill: var(--green); flex: none; }

  .slogan {
    position: absolute; left: 40px; top: 78px;
    color: var(--green); font-weight: 600; text-transform: uppercase;
  }
  .slogan span { display: block; white-space: nowrap; }
  .slogan .l1 { font-size: 36px; line-height: 44px; letter-spacing: 0.5px; }
  .slogan .l2 { font-size: 36px; line-height: 44px; margin-top: 14px; letter-spacing: 0.5px; }
  .slogan .l3 { font-size: 40px; line-height: 48px; margin-top: 28px; }
  .slogan .l4 { font-size: 98px; line-height: 92px; margin-top: 8px; letter-spacing: -1px; }
  .slogan .l5 { font-size: 38px; line-height: 44px; }
</style>
</head>
<body>
<main class="stage">

  <section class="card card--front" aria-label="Card front">
    <div class="relief-strip" role="img" aria-label="Faint white geometric wall-panel relief pattern"></div>

    <div class="brand">
      <div class="brand__mark"></div>
      <div class="brand__name">Ripplecraft<br>Facades</div>
    </div>

    <div class="person">
      <p class="person__name">Marcus Ellery</p>
      <p class="person__role">Managing Director</p>
    </div>

    <p class="address">12345, Address Goes Here<br>Country Name, 123456</p>

    <ul class="contacts">
      <li><svg viewBox="0 0 12 12"><path d="M3 0h6a1 1 0 0 1 1 1v10a1 1 0 0 1-1 1H3a1 1 0 0 1-1-1V1a1 1 0 0 1 1-1zm0 1.5v8h6v-8z"/></svg>123-456-7890</li>
      <li><svg viewBox="0 0 12 12"><path d="M2.5 0.5l2 2.2-1 1.4c.8 1.6 2 2.8 3.5 3.6l1.4-1 2.2 2-1.3 2.6C4.5 10.8 1.2 7.5.5 2z"/></svg>(044)-456-7890</li>
      <li><svg viewBox="0 0 12 12"><path d="M3 0h5v3H3zM1 4h10v6H9v2H3v-2H1zm3 4v3h4V8z"/></svg>123-456-7890</li>
      <li><svg viewBox="0 0 12 12"><path d="M0 2h12v1L6 7 0 3zm0 2.5l6 4 6-4V10H0z"/></svg>info@youremail.com</li>
      <li><svg viewBox="0 0 12 12"><circle cx="6" cy="6" r="5.5"/></svg>www.website.com</li>
    </ul>
  </section>

  <section class="card card--back" aria-label="Card back">
    <div class="relief-strip" role="img" aria-label="Faint white geometric wall-panel relief pattern"></div>
    <h1 class="slogan">
      <span class="l1">Decorative</span>
      <span class="l2">Panels for</span>
      <span class="l3">Interiors</span>
      <span class="l4">And</span>
      <span class="l5">Exteriors</span>
    </h1>
  </section>

</main>
</body>
</html>
```